Belmont Ridge Business Card Design Project

We have recently rebranded and would like to design new business cards that incorporate the corporate logo - double sided cards with corporate logo on one side and contact details on the other

Target Market(s)

Sophisticated and high net worth investors and finance industry professionals

Industry/Entity Type

Funds Management

Contact Information for Business Card

The card should prominently feature the company name and logo. Other details will be standard contact details for each staff member - name, address, phone, email, website

Colors
0054AA
0677BA
7BADD7
CADEEF
E8F1F8

Requirements
Must have
• Double-sided design with one side prominently featuring the corporate logo and the other side with all standard contact details

```html
<!DOCTYPE html>
<html lang="en">
<head>
<meta charset="utf-8">
<title>Belmont Ridge Business Card</title>
<link href="https://fonts.googleapis.com/css2?family=Lato:wght@400;700&display=swap" rel="stylesheet">
<style>
  :root {
    --navy: #204572;
    --card: #ffffff;
    --backdrop: #737373;
  }
  html, body {
    margin: 0;
    width: 1200px;
    height: 1200px;
    overflow: hidden;
    background: var(--backdrop);
    font-family: "Lato", sans-serif;
  }
  .card {
    position: absolute;
    left: 281px;
    width: 638px;
    height: 365px;
    border-radius: 21px;
    background: var(--card);
    overflow: hidden;
  }
  .card svg { display: block; width: 100%; height: 100%; }
  .card--front { top: 195px; }
  .card--back { top: 639px; }
  .fill-navy { fill: var(--navy); }
  .fill-white { fill: var(--card); }
  .stroke-white { stroke: var(--card); fill: none; }
  .brand { font-family: "Lato", sans-serif; font-weight: 700; fill: var(--navy); }
  .contact { font-family: "Lato", sans-serif; fill: var(--card); }
  .contact__name { font-weight: 700; font-size: 32px; }
  .contact__role { font-weight: 400; font-size: 20px; }
  .contact__line { font-weight: 400; font-size: 18px; letter-spacing: 0.8px; }
</style>
</head>
<body>

<section class="card card--front" aria-label="Business card, contact side">
  <svg viewBox="0 0 798 456" xmlns="http://www.w3.org/2000/svg">
    <!-- contact panel: plain diagonal block -->
    <polygon class="fill-navy" points="300,456 520,0 798,0 798,456"/>
    <line x1="272" y1="456" x2="492" y2="0" stroke="#204572" stroke-width="6"/>

    <!-- brand name -->
    <rect class="fill-navy" x="77" y="108" width="20" height="20"/>
    <text class="brand" x="108" y="128" font-size="30">Belmont Ridge</text>

    <!-- contact details -->
    <g class="contact" text-anchor="end">
      <text class="contact__name" x="754" y="194">DANIEL HARTLEY</text>
      <text class="contact__role" x="754" y="221">Founder &amp; CEO</text>
      <text class="contact__line" x="754" y="263">4870 Linden Avenue</text>
      <text class="contact__line" x="754" y="287">Hartwell, CT 06420</text>
      <text class="contact__line" x="727" y="328">(555) 214-3380</text>
      <text class="contact__line" x="727" y="356">(555) 214-3380</text>
      <text class="contact__line" x="727" y="383">info@belmontridge.com</text>
      <text class="contact__line" x="727" y="410">belmontridge.com</text>
    </g>

    <!-- icons -->
    <g class="icons">
      <path class="fill-white" d="M741,315 q2,-1 3,1 l2,4 q0,2 -2,2 q1,4 4,6 q1,-2 3,-1 l3,3 q1,2 -1,3 q-4,2 -8,-3 q-5,-6 -4,-15 z"/>
      <rect class="stroke-white" x="741" y="343" width="9" height="14" rx="1.5" stroke-width="2"/>
      <circle class="fill-white" cx="745.5" cy="354" r="1"/>
      <rect class="fill-white" x="739" y="373" width="14" height="10"/>
      <path d="M739,373 L746,379 L753,373" stroke="#204572" stroke-width="1.4" fill="none"/>
      <circle class="fill-white" cx="746" cy="404" r="7"/>
      <path d="M741,401 q3,2 5,0 q2,3 0,5 q-2,1 -1,4 M749,399 q-2,3 1,5 q2,0 3,2" stroke="#204572" stroke-width="1.3" fill="none"/>
    </g>
  </svg>
</section>

<section class="card card--back" aria-label="Business card, brand side">
  <svg viewBox="0 0 798 456" xmlns="http://www.w3.org/2000/svg">
    <rect class="fill-navy" x="168" y="240" width="30" height="30"/>
    <text class="brand" x="214" y="271" font-size="50" letter-spacing="1">Belmont Ridge</text>
  </svg>
</section>

</body>
</html>
```